Vellisant - Quality health delivered at your door

Vellisant offers home and Community Based Services for adults who wish to continue live independently in their communities. We increase accessibility to health care, reduce health care delivery gap, reduce mortality and morbidity, reduce health while promoting healthy living in the comfort of our patients communities or homes.

We provide on site services and deliver high quality healthcare at your door. Our experienced physicians coordinate care with our certified nurse practitioners and provide chronic care management, physical therapy, rehabilitation and medications management.

Target Market(s)

Older population living in independent living facilities

Industry/Entity Type

Health Care

Contact Information for Business Card

Vellisant

Number of Pages Required

4 page

Font styles to use
Sans Serif

Colors

Designer to choose colors to be used in the design.

```html
<!DOCTYPE html>
<html lang="en">
<head>
<meta charset="utf-8">
<title>Vellisant - Quality health delivered at your door</title>
<link rel="stylesheet" href="https://fonts.googleapis.com/css2?family=Noto+Serif:wght@400;700&family=Open+Sans:wght@400;600&display=swap">
<style>
  :root{
    --orange:#f8a01a;
    --orange-soft:rgba(248,160,26,.86);
    --olive:#6d8b25;
    --forest:#1f3401;
    --forest-deep:#1a2d00;
    --banner:rgba(31,54,4,.84);
    --white:#ffffff;
    --ink:#2a3a0a;
  }
  *{margin:0;padding:0;box-sizing:border-box}
  html,body{width:1200px;height:979px;overflow:hidden}
  body{position:relative;background:var(--forest);font-family:"Open Sans",sans-serif;color:var(--white)}
  a{color:inherit;text-decoration:none}

  /* Header */
  .site-header{position:absolute;left:0;top:0;width:1200px;height:156px;background:var(--orange)}
  .brand{position:absolute;left:76px;top:16px;width:180px;text-align:center}
  .brand-mark{display:block;width:94px;height:94px;margin:0 auto;border-radius:50%;background:var(--olive);border:5px solid var(--forest)}
  .brand-name{display:block;margin-top:4px;font-family:"Noto Serif",serif;font-size:26px;color:var(--forest);letter-spacing:.5px}

  .utility-bar{position:absolute;left:281px;top:0;width:552px;height:42px;background:var(--olive);clip-path:polygon(0 0,100% 0,94% 100%,7% 100%)}
  .utility-nav{position:absolute;left:330px;top:0;height:42px;display:flex;align-items:center;gap:26px;font-family:"Noto Serif",serif;font-size:14.5px;text-transform:uppercase}
  .utility-nav .is-active{color:var(--forest)}
  .contact-bar{position:absolute;left:800px;top:0;width:400px;height:42px;background:var(--forest);clip-path:polygon(0 0,100% 0,100% 100%,10% 100%)}
  .social{position:absolute;left:850px;top:12px;display:flex;gap:18px}
  .social span{width:18px;height:18px;border-radius:50%;background:var(--olive)}
  .social span:first-child{background:var(--white)}
  .phone{position:absolute;left:993px;top:0;height:42px;display:flex;align-items:center;gap:8px;font-family:"Noto Serif",serif;font-weight:700;font-size:16px}

  .main-nav{position:absolute;left:330px;top:88px;display:flex;gap:27px;font-family:"Noto Serif",serif;font-weight:700;font-size:14px;text-transform:uppercase}
  .nav-pointer{position:absolute;left:384px;top:146px;width:0;height:0;border-left:9px solid transparent;border-right:9px solid transparent;border-bottom:10px solid #d9d4c6}

  /* Hero */
  .hero{position:absolute;left:0;top:156px;width:1200px;height:521px}
  .hero-photo{position:absolute;inset:0;background:linear-gradient(100deg,#8a5a45 0%,#c9a88f 22%,#6fa3c9 32%,#d7c9c0 50%,#8c8f86 62%,#4f6b24 78%,#3e5d1c 100%)}
  .hero-banner{position:absolute;left:576px;top:141px;width:624px;height:166px;background:var(--banner);clip-path:polygon(0 0,100% 0,100% 100%,9% 100%)}
  .hero-title{position:absolute;right:80px;top:152px;text-align:right;font-family:"Noto Serif",serif;font-size:40px;line-height:62px}

  .service-bar{position:absolute;left:0;top:448px;width:1200px;height:73px;display:flex}
  .service{flex:1;display:flex;align-items:center;justify-content:space-between;padding:0 23px;background:var(--orange-soft);border-right:1px solid rgba(255,255,255,.75);font-family:"Noto Serif",serif;font-size:21px;text-transform:uppercase}
  .service:last-child{border-right:0}
  .service svg{flex:none}

  /* Intro */
  .intro{position:absolute;left:0;top:677px;width:1200px;height:240px;background:var(--forest-deep);text-align:center}
  .intro-title{margin-top:48px;font-family:"Noto Serif",serif;font-weight:400;font-size:42px;letter-spacing:1px}
  .intro-text{width:950px;margin:22px auto 0;font-size:15px;line-height:25px}

  /* Footer */
  .site-footer{position:absolute;left:0;top:917px;width:1200px;height:62px;background:var(--orange);border-top:1px solid rgba(255,255,255,.5);display:flex;align-items:center;justify-content:space-between;padding:0 78px}
  .copyright{font-family:"Noto Serif",serif;font-weight:700;font-size:14px}
  .copyright b{color:var(--forest)}
  .footer-nav{display:flex;gap:17px;font-size:14.5px;text-transform:uppercase}
</style>
</head>
<body>
  <header class="site-header">
    <a class="brand" href="#">
      <span class="brand-mark"></span>
      <span class="brand-name">VELLISANT</span>
    </a>
    <div class="utility-bar"></div>
    <nav class="utility-nav">
      <a class="is-active" href="#">Home</a>
      <a href="#">Rehabilition</a>
      <a href="#">Respite Care</a>
      <a href="#">Mindstep Learning</a>
    </nav>
    <div class="contact-bar"></div>
    <div class="social" aria-label="Social links"><span></span><span></span><span></span></div>
    <div class="phone">
      <svg width="16" height="16" viewBox="0 0 24 24" aria-hidden="true"><path fill="#fff" d="M6.6 10.8a15.1 15.1 0 0 0 6.6 6.6l2.2-2.2c.3-.3.7-.4 1-.2 1.1.4 2.3.6 3.6.6.6 0 1 .4 1 1V20c0 .6-.4 1-1 1A17 17 0 0 1 3 4c0-.6.4-1 1-1h3.5c.6 0 1 .4 1 1 0 1.3.2 2.5.6 3.6.1.3 0 .7-.2 1z"/></svg>
      555.214.0377
    </div>
    <nav class="main-nav">
      <a href="#">Assisted Living</a>
      <a href="#">Skilled Nursing</a>
      <a href="#">Independent Living</a>
      <a href="#">Home &amp; Community Based Living</a>
    </nav>
    <div class="nav-pointer"></div>
  </header>

  <section class="hero">
    <div class="hero-photo" role="img" aria-label="Caregiver leaning toward a smiling senior woman in a wheelchair outside a brick home"></div>
    <div class="hero-banner"></div>
    <h1 class="hero-title">Giving You the Freedom to<br>Live Life on your Term</h1>
    <nav class="service-bar">
      <a class="service" href="#">Health Services<svg width="22" height="22" viewBox="0 0 22 22" aria-hidden="true"><circle cx="11" cy="11" r="10" fill="#fff"/><path d="M6 11h9M11 6.5l4.5 4.5-4.5 4.5" stroke="#f8a01a" stroke-width="2.6" fill="none"/></svg></a>
      <a class="service" href="#">In Home Services<svg width="22" height="22" viewBox="0 0 22 22" aria-hidden="true"><circle cx="11" cy="11" r="10" fill="#fff"/><path d="M6 11h9M11 6.5l4.5 4.5-4.5 4.5" stroke="#f8a01a" stroke-width="2.6" fill="none"/></svg></a>
      <a class="service" href="#">Community Services<svg width="22" height="22" viewBox="0 0 22 22" aria-hidden="true"><circle cx="11" cy="11" r="10" fill="#fff"/><path d="M6 11h9M11 6.5l4.5 4.5-4.5 4.5" stroke="#f8a01a" stroke-width="2.6" fill="none"/></svg></a>
      <a class="service" href="#">All Services<svg width="22" height="22" viewBox="0 0 22 22" aria-hidden="true"><circle cx="11" cy="11" r="10" fill="#fff"/><path d="M6 11h9M11 6.5l4.5 4.5-4.5 4.5" stroke="#f8a01a" stroke-width="2.6" fill="none"/></svg></a>
    </nav>
  </section>

  <section class="intro">
    <h2 class="intro-title">STAY HOME</h2>
    <p class="intro-text">Vellisant offers home and Community Based Services for adults who wish to continue to live independently in the comfort of their communities. We provide on site services and deliver high quality healthcare at your door.&nbsp; Our experienced physicians coordinate care with our certified nurse practitioners and provide chronic care management, physical therapy, rehabilitation and medications management.</p>
  </section>

  <footer class="site-footer">
    <p class="copyright">© <b>VELLISANT</b> - 2017. All Rights Reserved.</p>
    <nav class="footer-nav">
      <a href="#">Home</a>
      <a href="#">About</a>
      <a href="#">Privacy Policy</a>
      <a href="#">Terms &amp; Conditions</a>
      <a href="#">Contact</a>
    </nav>
  </footer>
</body>
</html>
```